Business card for a Exhibition booth fabrication company

Hi. My company would like to change our corporate name card. We are an events and Exhibition stand builder company. We would like our corporate name card to resonate what we do. I need someone to create something unique that relates to the industry that I am in. The graphic designer should be creative to incorporate the elements of my industry and try to blend in well in the design of the card. Our aim is to ensure that we are unique and our card can look different from our competitors.
Updates

Target Market(s)

Marketing and events manager from all companies

Contact Information for Business Card

The business card should have the following details:
Name
Job Title
Email
Website

Colors

Designer to choose colors to be used in the design.

Requirements
Must have
• The card must be look something that is relevant to the service that I am providing. My website is: www.velmora-buildworks.com
• You can see my website to get more information on what service that I am doing
Nice to have
• On the back of my card, I would like to have a globe image with the incorporation of my company logo. This is to indicate that my services can be done in any part of the world.

```html
<!DOCTYPE html>
<html lang="en">
<head>
<meta charset="utf-8">
<title>Velmora Buildworks – Business Card</title>
<link rel="stylesheet" href="https://fonts.googleapis.com/css2?family=Montserrat:wght@400;500;600&display=swap">
<style>
:root{
  --stage:#1c1c1d;
  --card-dark:#2e2d2f;
  --card-light:#ffffff;
  --red:#e8222a;
  --ink:#3a3a3c;
  --grey:#6d6e70;
  --rule:#8a8b8d;
  --text-light:#f1f1f1;
}
*{margin:0;padding:0;box-sizing:border-box}
html,body{width:1200px;height:880px;overflow:hidden;background:var(--stage);font-family:"Montserrat",sans-serif}
.canvas{position:relative;width:1200px;height:880px}
.card{position:absolute;width:640px;height:366px;border-radius:22px;overflow:hidden}

/* back side */
.card-back{left:70px;top:60px;background:var(--card-dark)}
.globe-map{position:absolute;left:90px;top:30px;width:460px;height:240px;border-radius:40%;
  background:radial-gradient(ellipse at center,#3a393b 0%,#323133 60%,rgba(46,45,47,0) 100%)}
.services{position:absolute;top:92px;left:0;width:100%;display:flex;justify-content:center}
.service-list{list-style:none;color:var(--text-light);font-size:14px;line-height:24px}
.service-list li{display:flex;align-items:center;gap:10px}
.service-list li::before{content:"";width:8px;height:8px;background:var(--red);transform:rotate(45deg);flex:none}
.service-list.left{text-align:right;padding-right:22px;padding-top:10px}
.service-list.left li{flex-direction:row-reverse}
.service-divider{width:1px;height:116px;background:#bdbdbd}
.service-list.right{padding-left:22px}
.experience-band{position:absolute;left:0;right:0;bottom:38px;height:40px;background:var(--red);
  border-top:3px solid #fff;box-shadow:0 -5px 0 var(--red);color:#fff;font-size:14px;letter-spacing:.5px;
  display:flex;align-items:center;justify-content:center}

/* front side */
.card-front{left:490px;top:456px;background:var(--card-light)}
.brand{position:absolute;left:40px;top:96px;width:260px;display:flex;flex-direction:column;align-items:center;gap:12px}
.brand-dot{width:46px;height:46px;border-radius:50%;background:var(--red)}
.brand-name{font-size:15px;font-weight:600;letter-spacing:2px;color:var(--grey);white-space:nowrap}
.front-divider{position:absolute;left:330px;top:70px;width:1px;height:130px;background:var(--red)}
.contact{position:absolute;left:356px;top:66px}
.person-name{font-size:24px;font-weight:500;color:var(--red);line-height:1}
.person-role{font-size:14px;color:var(--grey);margin-top:2px}
.contact-list{list-style:none;margin-top:14px;font-size:14px;color:var(--ink);line-height:24px}
.contact-list li{display:flex;align-items:center;gap:10px}
.contact-list svg{width:13px;height:13px;fill:var(--red);flex:none}
.contact-list .web-accent{color:var(--red)}
.tagline-band{position:absolute;left:0;right:0;bottom:34px;height:40px;background:var(--red);
  box-shadow:0 -6px 0 #fff,0 -9px 0 var(--rule);color:#fff;font-size:15px;letter-spacing:1.5px;
  display:flex;align-items:center;justify-content:center}
</style>
</head>
<body>
<main class="canvas">

  <section class="card card-back" aria-label="Card back">
    <div class="globe-map" role="img" aria-label="Faint dotted world map showing global service reach"></div>
    <div class="services">
      <ul class="service-list left">
        <li>Exhibition Booth Fabrication</li>
        <li>Outdoor Booth Setup</li>
        <li>Interior Design</li>
        <li>Installation and Dismantle</li>
      </ul>
      <div class="service-divider"></div>
      <ul class="service-list right">
        <li>Exhibition Management</li>
        <li>Shell Scheme Display Booth</li>
        <li>Custom Stand Design</li>
        <li>Exhibition Furniture and Equipment</li>
        <li>Exhibition Project Management</li>
      </ul>
    </div>
    <div class="experience-band">OVER 20 YEARS EXPERIENCE OF EXHIBITION STAND SERVICES</div>
  </section>

  <section class="card card-front" aria-label="Card front">
    <div class="brand">
      <span class="brand-dot"></span>
      <span class="brand-name">VELMORA BUILDWORKS</span>
    </div>
    <div class="front-divider"></div>
    <div class="contact">
      <p class="person-name">Liam Carter</p>
      <p class="person-role">Director</p>
      <ul class="contact-list">
        <li><svg viewBox="0 0 16 16"><path d="M4 1l3 3-2 2c1 2 3 4 5 5l2-2 3 3-2 3C7 15 1 9 1 3z"/></svg>0123 555 014</li>
        <li><svg viewBox="0 0 16 16"><path d="M1 3h14v10H1z M1 3l7 6 7-6" stroke="#fff" stroke-width="1.2"/></svg>info@velmoramail.com</li>
        <li><svg viewBox="0 0 16 16"><circle cx="8" cy="8" r="7"/><path d="M1 8h14M8 1c-3 4-3 10 0 14M8 1c3 4 3 10 0 14" stroke="#fff" fill="none" stroke-width="1"/></svg><span>www.<span class="web-accent">velmora-buildworks</span>.com</span></li>
      </ul>
    </div>
    <div class="tagline-band">Building Conceptions Into Reality</div>
  </section>

</main>
</body>
</html>
```